Cover for Lanterns Along the Quiet Shore of Being

Cover for a book that describes everything that happens to a person, from pre-birth life plans through growing in compassion and wisdom to death and living in the afterlife. The information is revealed in messages from people living in the life after this life. The title is Lessons Gathered From Every Season of Your Existence: Shared by Voices Dwelling Beyond the Veil. Author is T. Wesley Prandt. Book size is 6 by 9.

Target Market(s)

General

Font styles to use
Serif

```html
<!DOCTYPE html>
<html lang="en">
<head>
<meta charset="utf-8">
<title>Lessons Gathered From Every Season of Your Existence — Book Cover</title>
<link href="https://fonts.googleapis.com/css2?family=Montserrat:wght@400&family=Oswald:wght@300;500&display=swap" rel="stylesheet">
<style>
  :root {
    --stage: #4f4f4f;
    --sky-deep: #1d3a78;
    --sky-mid: #5b7fae;
    --glow: #fbfaf2;
    --gold: #e6c46a;
    --haze: #b9ab8c;
    --ridge: #1a1a18;
    --ink-navy: #12275a;
    --paper-white: #ffffff;
    --subtitle-ink: #f4f6fb;
  }
  * { margin: 0; padding: 0; box-sizing: border-box; }
  html, body {
    width: 1200px;
    height: 889px;
    overflow: hidden;
    background: var(--stage);
  }
  .stage {
    width: 1200px;
    height: 889px;
    display: flex;
    align-items: center;
    justify-content: center;
  }
  .book-cover {
    position: relative;
    width: 548px;
    height: 822px;
    overflow: hidden;
    box-shadow: 0 10px 30px rgba(0, 0, 0, 0.35);
  }
  .cover-art {
    position: absolute;
    inset: 0;
    background:
      radial-gradient(ellipse 70% 28% at 50% 52%, var(--glow) 0%, rgba(251, 250, 242, 0.85) 35%, rgba(251, 250, 242, 0) 100%),
      linear-gradient(180deg,
        var(--sky-deep) 0%,
        var(--sky-mid) 18%,
        #c9d3df 36%,
        var(--glow) 50%,
        var(--gold) 64%,
        var(--haze) 74%,
        #6f6a5c 82%,
        var(--ridge) 90%,
        #070707 100%);
  }
  .title-block {
    position: absolute;
    top: 88px;
    left: 0;
    right: 0;
    text-align: center;
  }
  .kicker {
    font-family: "Montserrat", sans-serif;
    font-weight: 400;
    font-size: 15px;
    color: var(--subtitle-ink);
    letter-spacing: 0.01em;
    text-shadow: 0 1px 3px rgba(0, 0, 0, 0.25);
  }
  .main-title {
    font-family: "Oswald", sans-serif;
    font-weight: 500;
    color: var(--ink-navy);
    text-transform: uppercase;
    line-height: 0.86;
    margin-top: 10px;
  }
  .main-title .line-lead {
    display: block;
    font-size: 168px;
    letter-spacing: -0.01em;
  }
  .main-title .line-rest {
    display: block;
    font-size: 92px;
    letter-spacing: -0.02em;
    margin-top: 4px;
  }
  .author {
    position: absolute;
    left: 0;
    right: 0;
    top: 742px;
    text-align: center;
    font-family: "Oswald", sans-serif;
    font-weight: 300;
    font-size: 26px;
    letter-spacing: 0.42em;
    color: var(--paper-white);
    text-transform: uppercase;
  }
</style>
</head>
<body>
  <main class="stage">
    <section class="book-cover">
      <div class="cover-art" role="img" aria-label="Photograph of a sunlit sky breaking through clouds above misty forested hills, with a bare branch and a small perched bird in silhouette"></div>
      <header class="title-block">
        <p class="kicker">Lessons Gathered From Every Season of</p>
        <h1 class="main-title">
          <span class="line-lead">Your</span>
          <span class="line-rest">Existence</span>
        </h1>
      </header>
      <p class="author">T. Wesley Prandt</p>
    </section>
  </main>
</body>
</html>
```